Tolbek cards

I want a simple business card that pops.
Logo on one side.
On side two i want.
"Are you thinking about a new building on your property, or renovating an existing structure? Contact".....
Owners Name: Dale Whitacre
Owners Phone number: 610-555-0187
Address:4076 Copper Ridge RD, Ashvale, PA 16940
Committed to Quality, Service, and Integrity

```html
<!DOCTYPE html>
<html lang="en">
<head>
<meta charset="utf-8">
<title>Tolbek Builders LLC – Business Card</title>
<link href="https://fonts.googleapis.com/css2?family=Montserrat:wght@400;500;700;800&display=swap" rel="stylesheet">
<style>
  :root {
    --bg: #9a9a9a;
    --brown-dark: #412c1b;
    --brown-name: #5e4128;
    --ink: #2b2b2b;
    --white: #ffffff;
  }
  * { box-sizing: border-box; margin: 0; padding: 0; }
  html, body { width: 1200px; height: 1108px; overflow: hidden; }
  body {
    background: var(--bg);
    font-family: "Montserrat", Arial, sans-serif;
    position: relative;
  }
  .card {
    position: absolute;
    left: 242px;
    width: 716px;
    height: 409px;
    border-radius: 26px;
    overflow: hidden;
  }
  .card-front { top: 119px; background: var(--brown-dark); }
  .card-back { top: 581px; background: var(--white); }

  /* Front */
  .front-brand {
    position: absolute;
    left: 0; right: 0; top: 110px;
    text-align: center;
    color: var(--white);
    font-weight: 800;
    letter-spacing: 1px;
  }
  .front-brand .mark {
    width: 70px; height: 70px;
    background: var(--white);
    margin: 0 auto 22px;
  }
  .front-brand .name { font-size: 84px; line-height: 1; }
  .front-brand .sub { font-size: 28px; letter-spacing: 3px; margin-top: 10px; }

  /* Back */
  .intro {
    position: absolute;
    left: 0; right: 0; top: 20px;
    text-align: center;
    font-size: 17px;
    line-height: 29px;
    color: var(--ink);
    letter-spacing: 0.4px;
  }
  .back-brand {
    position: absolute;
    left: 61px; width: 280px; top: 100px;
    text-align: center;
    color: var(--brown-dark);
    font-weight: 800;
  }
  .back-brand .mark {
    width: 60px; height: 60px;
    background: var(--brown-dark);
    margin: 0 auto 18px;
  }
  .back-brand .name { font-size: 60px; line-height: 1; }
  .back-brand .sub { font-size: 20px; letter-spacing: 2px; margin-top: 6px; }

  .divider {
    position: absolute;
    left: 367px; top: 94px;
    width: 2px; height: 220px;
    background: var(--brown-dark);
  }
  .contact {
    position: absolute;
    left: 397px; top: 90px;
    color: var(--ink);
    font-size: 17px;
    letter-spacing: 0.4px;
  }
  .contact .person { font-size: 30px; font-weight: 700; color: var(--brown-name); line-height: 36px; }
  .contact .role { margin-top: 2px; line-height: 22px; }
  .contact .address { margin-top: 16px; line-height: 29px; }
  .contact ul { list-style: none; margin-top: 12px; }
  .contact li { display: flex; align-items: center; gap: 9px; line-height: 28.5px; }
  .contact svg { width: 15px; height: 15px; fill: var(--ink); flex: none; }

  .motto {
    position: absolute;
    left: 0; right: 0; top: 359px;
    height: 25px;
    background: var(--brown-dark);
    color: var(--white);
    text-align: center;
    font-size: 17px;
    line-height: 25px;
    letter-spacing: 0.4px;
  }
</style>
</head>
<body>
  <section class="card card-front">
    <div class="front-brand">
      <div class="mark"></div>
      <div class="name">TOLBEK</div>
      <div class="sub">BUILDERS LLC</div>
    </div>
  </section>

  <section class="card card-back">
    <p class="intro">Are you thinking about a new building on your<br>property, or renovating an existing structure? Contact</p>

    <div class="back-brand">
      <div class="mark"></div>
      <div class="name">TOLBEK</div>
      <div class="sub">BUILDERS LLC</div>
    </div>

    <div class="divider"></div>

    <div class="contact">
      <div class="person">Dale Whitacre</div>
      <div class="role">Owner</div>
      <div class="address">4076 Copper Ridge RD,<br>Ashvale, PA 16940</div>
      <ul>
        <li>
          <svg viewBox="0 0 16 16" aria-hidden="true"><path d="M1 6c0-2 3-4 7-4s7 2 7 4v1h-4V5.5C10 5 9 5 8 5s-2 0-3 .5V7H1zM4 8h8l2 6H2z"/></svg>
          610-555-0187
        </li>
        <li>
          <svg viewBox="0 0 16 16" aria-hidden="true"><path d="M1 3h14v10H1zM2 4.2V12h12V4.2L8 9z"/><path d="M1 3l7 6 7-6z"/></svg>
          info@tolbek.buildersllc
        </li>
        <li>
          <svg viewBox="0 0 16 16" aria-hidden="true"><path d="M8 1a7 7 0 1 0 0 14A7 7 0 0 0 8 1zm0 1.5a5.5 5.5 0 0 1 4.6 2.5H10l-1 2 2 2-1 3 -2 1.5V11L6 9.5 4 8 3.2 5.5A5.5 5.5 0 0 1 8 2.5z"/></svg>
          www.tolbek.buildersllc
        </li>
      </ul>
    </div>

    <div class="motto">Committed to Quality, Service, and Integrity</div>
  </section>
</body>
</html>
```